KVM Contracting services . Building and maintenance services, optic fibre installation

Business cards and logo design.I need a logo that I can use on business cards ,workwear and on my vehicles. I would like the KVM to be the main or larger text and contracting services to be the smaller or less important text.I like monograms, modern designs and repeating patterns symbols. I am also a Gemini and my favourite number is 22 so if this can be any inspiration to help with the design. Am thinking of the using German flag colours as a his is my family’s heritage. And the other 2 main colours I wear is black and white.But any ideas are appreciated.I do not need a design that is trade specific but a design that could be used for any business.

Target Market(s)

General public

Contact Information for Business Card

KVM Contracting Services ( front of business card)

(Back of business card)
Darren Holtwick
0451907326
Maintenance services
Optic fibre and data installation

Logo Text

Logo can just be pattern or monogram or incorporate KVM . I like the gemini star sign and the number 22

Colors
ec1f27
000000
fbee3e
ffffff

Requirements
Must have
• Logo and KVM Contracting Services on the front of business card
Nice to have
• Possible use of German flag colours.
• Modern design.
• Design to be able to be used on black or white background as I want to put it on clothing

```html
<!DOCTYPE html>
<html lang="en">
<head>
<meta charset="utf-8">
<title>KVM Contracting Services – Business Card</title>
<link rel="stylesheet" href="https://fonts.googleapis.com/css2?family=Open+Sans:wght@400;700;800&display=swap">
<style>
  :root {
    --brand-red: #ec1f27;
    --brand-black: #000000;
    --brand-white: #ffffff;
    --ink: #1a1a1a;
    --backdrop: #e6e6e6;
    --card-shadow: rgba(0, 0, 0, 0.18);
  }

  * { box-sizing: border-box; margin: 0; padding: 0; }

  html, body {
    width: 1200px;
    height: 782px;
    overflow: hidden;
  }

  body {
    background: var(--backdrop);
    font-family: "Open Sans", Arial, sans-serif;
    position: relative;
  }

  .card {
    position: absolute;
    left: 320px;
    width: 560px;
    height: 320px;
    box-shadow: 0 6px 18px var(--card-shadow);
    overflow: hidden;
  }

  .card--front {
    top: 46px;
    background: var(--brand-red);
    display: flex;
    align-items: center;
    justify-content: center;
  }

  .card--back {
    top: 416px;
    background: var(--brand-white);
  }

  .card--back::after {
    content: "";
    position: absolute;
    left: 0; right: 0; bottom: 0;
    height: 12px;
    background: var(--brand-red);
  }

  /* Logo lockup: plain mark + wordmark */
  .lockup {
    display: flex;
    align-items: center;
    gap: 18px;
  }

  .lockup__mark {
    border-radius: 50%;
    flex: none;
  }

  .lockup__words {
    display: flex;
    flex-direction: column;
    font-weight: 800;
    line-height: 1;
  }

  .lockup__name {
    font-size: 84px;
    letter-spacing: 6px;
  }

  .lockup__tagline {
    font-size: 15px;
    letter-spacing: 0.5px;
    text-transform: uppercase;
    margin-top: 2px;
  }

  .lockup--on-red .lockup__mark {
    width: 78px; height: 78px;
    background: var(--brand-white);
  }
  .lockup--on-red .lockup__words { color: var(--brand-white); }

  .lockup--on-white {
    position: absolute;
    right: 36px;
    top: 96px;
    gap: 12px;
  }
  .lockup--on-white .lockup__mark {
    width: 56px; height: 56px;
    background: var(--brand-black);
  }
  .lockup--on-white .lockup__words { color: var(--brand-red); }
  .lockup--on-white .lockup__name { font-size: 60px; letter-spacing: 4px; }
  .lockup--on-white .lockup__tagline { font-size: 11px; }

  /* Contact details */
  .contact {
    position: absolute;
    left: 34px;
    top: 118px;
    color: var(--ink);
  }

  .contact__name {
    color: var(--brand-red);
    font-weight: 700;
    font-size: 15px;
    text-transform: uppercase;
    letter-spacing: 0.3px;
  }

  .contact__phone {
    font-size: 17px;
    margin-bottom: 12px;
  }

  .contact__services {
    list-style: none;
    font-size: 14px;
    line-height: 1.35;
  }
</style>
</head>
<body>

  <section class="card card--front" aria-label="Business card front">
    <div class="lockup lockup--on-red">
      <span class="lockup__mark" aria-hidden="true"></span>
      <div class="lockup__words">
        <span class="lockup__name">KVM</span>
        <span class="lockup__tagline">Contracting Services</span>
      </div>
    </div>
  </section>

  <section class="card card--back" aria-label="Business card back">
    <div class="contact">
      <p class="contact__name">Darren Holtwick</p>
      <p class="contact__phone">0451907326</p>
      <ul class="contact__services">
        <li>Maintenance services</li>
        <li>Optic fibre and data installation</li>
      </ul>
    </div>

    <div class="lockup lockup--on-white">
      <span class="lockup__mark" aria-hidden="true"></span>
      <div class="lockup__words">
        <span class="lockup__name">KVM</span>
        <span class="lockup__tagline">Contracting Services</span>
      </div>
    </div>
  </section>

</body>
</html>
```